Moderne Visitenkarten für Medizintechnikfirma
Zielgruppe
Vertriebsfirma von moderner und innovativer Medizintechnik
Zielgruppe: Ärzte, Kliniken, Medizintechnikfirmen, Patienten
Aufgabenstellung
Besonderes, modernes, auffälliges und ansprechendes Design ohne überladen oder aufdringlich zu sein
Farbenorientierung kann am Logo und der Website geschehen. Wenn zum Logo harmonierend, sind aber auch andere Farben gerne gesehen.
Format: eher horizontal, vertikal aber auch möglich, abgerundete Ecken einplanen
Wenn möglich folgende Infos bitte schon auf die Karten bringen (pro Person eine Karte):
Konrad Faltermann (CEO)
konrad.faltermann@vitalis-partner.de
(Vitalis Partner GmbH
Lindenhof 12
26210 Grünstedt)
www.vitalis-partner.de
info@vitalis-partner.de
Jonas Prasken (CoS)
jonas.prasken@vitalis-partner.de
Die allgemeinen Firmeninfos können deutlich kleiner sein. Anschrift nur wenn es dadurch nicht zu viel werden würde.

```html
<!DOCTYPE html>
<html lang="de">
<head>
<meta charset="utf-8">
<title>Vitalis Partner – Visitenkarten</title>
<link rel="stylesheet" href="https://fonts.googleapis.com/css2?family=Raleway:wght@400;500&display=swap">
<style>
  :root {
    --purple: #53437f;
    --purple-soft: #6a5c96;
    --orange: #e9562b;
    --ink: #4b4568;
    --card-light: #ffffff;
    --card-dark: #d9d9db;
    --card-edge: #c4c4c8;
    --label: #6f6f6f;
    --page: #ffffff;
  }
  * { box-sizing: border-box; margin: 0; padding: 0; }
  html, body {
    width: 995px;
    height: 1200px;
    overflow: hidden;
    background: var(--page);
    font-family: "Raleway", sans-serif;
  }
  .sheet {
    position: relative;
    width: 995px;
    height: 1200px;
  }
  .format-label {
    position: absolute;
    top: 0;
    left: 0;
    width: 100%;
    text-align: center;
    font-size: 22px;
    color: var(--label);
    line-height: 30px;
  }
  .card {
    position: absolute;
    left: 25px;
    width: 945px;
    height: 535px;
    border: 1px solid var(--card-edge);
    background: linear-gradient(110deg, var(--card-light) 0%, #f1f1f2 40%, var(--card-dark) 100%);
  }
  .card--ceo { top: 62px; }
  .card--cos { top: 655px; }

  .brand {
    position: absolute;
    left: 150px;
    top: 130px;
    display: flex;
    align-items: center;
    gap: 34px;
  }
  .brand__dot {
    width: 70px;
    height: 70px;
    border-radius: 50%;
    background: var(--purple);
  }
  .brand__name {
    font-size: 76px;
    font-weight: 500;
    color: var(--purple);
    letter-spacing: -0.5px;
    line-height: 1;
  }

  .company {
    position: absolute;
    left: 37px;
    top: 352px;
    font-size: 26px;
    line-height: 29px;
    color: var(--purple-soft);
  }

  .person {
    position: absolute;
    right: 25px;
    top: 345px;
    text-align: right;
  }
  .person__name {
    font-size: 40px;
    font-weight: 500;
    color: var(--orange);
    line-height: 50px;
  }
  .person__rule {
    display: block;
    width: 370px;
    height: 2px;
    margin: 14px 0 16px auto;
    background: linear-gradient(90deg, rgba(120,120,130,0) 0%, #9a9aa3 60%, #8a8a94 100%);
  }
  .person__contact {
    font-size: 26px;
    line-height: 36px;
    color: var(--ink);
  }
</style>
</head>
<body>
<main class="sheet">
  <p class="format-label">size: 90/50 mm</p>

  <article class="card card--ceo">
    <div class="brand">
      <span class="brand__dot"></span>
      <span class="brand__name">Vitalis Partner</span>
    </div>
    <address class="company" style="font-style:normal">
      Lindenhof 12<br>
      26210 Grünstedt)<br>
      www.vitalis-partner.de<br>
      info@vitalis-partner.de<br>
      0800-5550190
    </address>
    <div class="person">
      <p class="person__name">Konrad Faltermann (CEO)</p>
      <span class="person__rule"></span>
      <p class="person__contact">+4917655501234<br>konrad.faltermann@vitalis-partner.de</p>
    </div>
  </article>

  <article class="card card--cos">
    <div class="brand">
      <span class="brand__dot"></span>
      <span class="brand__name">Vitalis Partner</span>
    </div>
    <address class="company" style="font-style:normal">
      Lindenhof 12<br>
      26210 Grünstedt)<br>
      www.vitalis-partner.de<br>
      info@vitalis-partner.de<br>
      0800-5550190
    </address>
    <div class="person">
      <p class="person__name">Jonas Prasken (CoS)</p>
      <span class="person__rule"></span>
      <p class="person__contact">+4915255507218<br>jonas.prasken@vitalis-partner.de</p>
    </div>
  </article>
</main>
</body>
</html>
```